Hvac and insulation company needs good looking business card design

We are hvac and insulation company and looking for a new business cards that look to today standards designs

Target Market(s)

homeowners

Industry/Entity Type

Hvac

Contact Information for Business Card

Name: Walter Brinoku
Home comfort consultant
address: 4827 Dunmore St #215 Oakland, CA 94619
office: 888-316-2790
cell: 510-742-3185
Lic.# 584261
Email: walter@corvane-hvac.com
Web: corvane-hvac.com

Requirements
Must have
• clean and sleek look
Nice to have
• simple with a clean look
Should not have
• to busy business card

```html
<!DOCTYPE html>
<html lang="en">
<head>
<meta charset="utf-8">
<title>Corvane Home Solutions — Business Card</title>
<link rel="stylesheet" href="https://fonts.googleapis.com/css2?family=Source+Sans+3:wght@400;600&display=swap">
<style>
  :root {
    --backdrop: #1daf99;
    --brand-orange: #f28424;
    --card-white: #ffffff;
    --ink: #2b2b2b;
  }
  * { margin: 0; padding: 0; box-sizing: border-box; }
  html, body {
    width: 1200px; height: 802px; overflow: hidden;
    background: var(--backdrop);
    font-family: "Source Sans 3", "Myriad Pro", sans-serif;
  }
  .stage { position: relative; width: 1200px; height: 802px; }
  .card {
    position: absolute; top: 274px;
    width: 442px; height: 265px;
  }
  .card--front { left: 136px; background: var(--card-white); }
  .card--back  { left: 624px; background: var(--brand-orange); }

  .holder { position: absolute; left: 43px; top: 27px; }
  .holder__name {
    color: var(--brand-orange); font-weight: 600;
    font-size: 15px; letter-spacing: 0.2px; text-transform: uppercase;
  }
  .holder__title { color: var(--ink); font-size: 12.5px; margin-top: 1px; }

  .contacts { position: absolute; left: 43px; top: 86px; list-style: none; }
  .contacts li {
    display: flex; align-items: center; gap: 6px;
    color: var(--ink); font-size: 12.5px; line-height: 15.8px;
  }
  .contacts svg { width: 9px; height: 9px; fill: var(--brand-orange); flex: none; }

  .address {
    position: absolute; left: 43px; top: 171px;
    color: var(--ink); font-size: 12.5px; line-height: 15.8px; font-style: normal;
  }
  .license {
    position: absolute; left: 43px; top: 219px;
    color: var(--brand-orange); font-size: 12.5px;
  }

  .wordmark-vertical {
    position: absolute; left: 330px; top: 243px;
    transform: rotate(-90deg); transform-origin: 0 0;
    color: var(--brand-orange); font-weight: 600; white-space: nowrap;
  }
  .wordmark-vertical__name { font-size: 58px; line-height: 50px; letter-spacing: -1px; }
  .wordmark-vertical__tag { font-size: 15px; letter-spacing: 4.6px; line-height: 18px; padding-left: 56px; }

  .wordmark {
    position: absolute; left: 50px; top: 96px;
    display: flex; align-items: center; gap: 16px;
    color: var(--card-white); font-weight: 600;
  }
  .wordmark__dot { width: 62px; height: 62px; border-radius: 50%; background: var(--card-white); }
  .wordmark__name { font-size: 56px; line-height: 46px; letter-spacing: -0.5px; }
  .wordmark__tag { font-size: 16px; letter-spacing: 4px; line-height: 20px; padding-left: 3px; }
</style>
</head>
<body>
<main class="stage">
  <section class="card card--front">
    <header class="holder">
      <h1 class="holder__name">Walter Brinoku</h1>
      <p class="holder__title">Home Comfort Consultant</p>
    </header>

    <ul class="contacts">
      <li><svg viewBox="0 0 10 10" aria-hidden="true"><path d="M0 3.5Q5 0 10 3.5L9 5H7.2L6.8 3.8H3.2L2.8 5H1Z"/><rect x="1.5" y="5.5" width="7" height="3.5" rx="0.6"/></svg>888-316-2790</li>
      <li><svg viewBox="0 0 10 10" aria-hidden="true"><path d="M2.5 0h5a.8.8 0 0 1 .8.8v8.4a.8.8 0 0 1-.8.8h-5a.8.8 0 0 1-.8-.8V.8A.8.8 0 0 1 2.5 0Zm.4 1.2v6.6h4.2V1.2Z"/></svg>510-742-3185</li>
      <li><svg viewBox="0 0 10 10" aria-hidden="true"><path d="M0 2h10v6.5H0Zm1 1v.3l4 2.8 4-2.8V3Z"/></svg>walter@corvane-hvac.com</li>
      <li><svg viewBox="0 0 10 10" aria-hidden="true"><circle cx="5" cy="5" r="5"/></svg>corvane-hvac.com</li>
    </ul>

    <address class="address">4827 Dunmore St #215<br>Oakland, CA 94619</address>
    <p class="license">Lic.# 584261</p>

    <div class="wordmark-vertical">
      <div class="wordmark-vertical__name">corvane</div>
      <div class="wordmark-vertical__tag">home solutions</div>
    </div>
  </section>

  <section class="card card--back">
    <div class="wordmark">
      <span class="wordmark__dot" aria-hidden="true"></span>
      <div>
        <div class="wordmark__name">corvane</div>
        <div class="wordmark__tag">home solutions</div>
      </div>
    </div>
  </section>
</main>
</body>
</html>
```